Business card for a new cabinet shop company named Veloran Cabinets for high end cabinets

Design a business card, thinking dark rich green with colours to speak of high end luxury ie; cream, gold, black possibly

Mitchell Tarrowby
Director Craftsman
Email: info@veloranjoinery-example.com.au
Instagram : @veloran.cabinets

```html
<!DOCTYPE html>
<html lang="en">
<head>
<meta charset="utf-8">
<title>Veloran Cabinets – Business Card</title>
<link rel="stylesheet" href="https://fonts.googleapis.com/css2?family=Montserrat:wght@400;600&display=swap">
<style>
  :root {
    --backdrop: #9a9a9a;
    --card-black: #141414;
    --pattern-deep: #0c0c0c;
    --pattern-dark: #161616;
    --pattern-mid: #2a2a2a;
    --pattern-silver: #6e6e6e;
    --sheen: rgba(255, 255, 255, 0.16);
    --gold: #c9a862;
    --cream: #f2efe8;
  }
  * { margin: 0; padding: 0; box-sizing: border-box; }
  html, body {
    width: 1200px;
    height: 1108px;
    overflow: hidden;
    background: var(--backdrop);
    font-family: "Montserrat", Arial, sans-serif;
  }
  .canvas { position: relative; width: 1200px; height: 1108px; }
  .card {
    position: absolute;
    left: 242px;
    width: 715px;
    height: 409px;
    border-radius: 30px;
    background: var(--card-black);
    overflow: hidden;
  }
  .card--front { top: 119px; }
  .card--back { top: 580px; }

  .front-pattern {
    position: absolute;
    inset: 0;
    background:
      linear-gradient(118deg, transparent 0%, transparent 36%, var(--sheen) 44%, rgba(255,255,255,0.07) 52%, transparent 62%, transparent 100%),
      linear-gradient(118deg, var(--pattern-silver) 0%, var(--pattern-mid) 34%, var(--pattern-dark) 40%, var(--pattern-mid) 55%, var(--pattern-dark) 78%, var(--pattern-deep) 100%);
  }

  .brand-name {
    position: absolute;
    left: 48px;
    top: 0;
    width: 285px;
    height: 100%;
    display: flex;
    align-items: center;
    color: var(--gold);
    font-weight: 600;
    font-size: 29px;
    letter-spacing: 0.4px;
    white-space: nowrap;
  }
  .divider {
    position: absolute;
    left: 350px;
    top: 135px;
    width: 2px;
    height: 139px;
    background: var(--gold);
  }
  .contact-block {
    position: absolute;
    left: 375px;
    top: 132px;
  }
  .person-name {
    color: var(--gold);
    font-weight: 600;
    font-size: 30px;
    line-height: 36px;
    letter-spacing: 0.3px;
    white-space: nowrap;
  }
  .person-title {
    color: var(--cream);
    font-weight: 400;
    font-size: 18px;
    line-height: 26px;
    margin-top: 2px;
  }
  .contact-list { list-style: none; margin-top: 25px; }
  .contact-item {
    display: flex;
    align-items: center;
    gap: 9px;
    color: var(--cream);
    font-size: 14.5px;
    line-height: 28px;
    white-space: nowrap;
  }
  .contact-icon { width: 15px; height: 15px; flex: none; }
</style>
</head>
<body>
<main class="canvas">
  <section class="card card--front" aria-label="Card front">
    <div class="front-pattern" role="img" aria-label="Repeating brand mark pattern in silver foil on black gloss with a diagonal light sheen"></div>
  </section>

  <section class="card card--back" aria-label="Card back">
    <div class="brand-name">Veloran Cabinets</div>
    <div class="divider"></div>
    <div class="contact-block">
      <h1 class="person-name">Mitchell Tarrowby</h1>
      <p class="person-title">Director Craftsman</p>
      <ul class="contact-list">
        <li class="contact-item">
          <svg class="contact-icon" viewBox="0 0 16 16" aria-hidden="true">
            <rect x="1" y="4" width="14" height="9" fill="var(--gold)"/>
            <path d="M1 4 L8 9.5 L15 4" fill="none" stroke="var(--card-black)" stroke-width="1.2"/>
          </svg>
          <span>info@veloranjoinery-example.com.au</span>
        </li>
        <li class="contact-item">
          <svg class="contact-icon" viewBox="0 0 16 16" aria-hidden="true">
            <circle cx="8" cy="8" r="6.5" fill="none" stroke="var(--gold)" stroke-width="1.6"/>
          </svg>
          <span>@veloran.cabinets</span>
        </li>
      </ul>
    </div>
  </section>
</main>
</body>
</html>
```